Private Investigation Business Card Design

I need a business card for a new private investigation company named Brisk Inquiries. I perform mainly surveillance jobs, vehicle repossessions, document serves etc. The final design should aim for a professional look. The logo has a magnifying glass with stick man arms and legs and is in a running action to show the "Brisk" aspect of the name. If the colour scheme could remain the same as the website www.briskinquiries-demo.com.au with silvers,blacks and a couple electric blue highlights.
Industry/Entity Type
Business
Contact Information for Business Card
Morgan Kellaway
Brisk Inquiries
0487316204
PO Box 58, Carnwell NSW 2291
info@briskinquiries-demo.com.au
www.briskinquiries-demo.com.au
Look and feel

```html
<!DOCTYPE html>
<html lang="en">
<head>
<meta charset="utf-8">
<title>Brisk Inquiries Business Card</title>
<link href="https://fonts.googleapis.com/css2?family=Open+Sans:ital,wght@0,400;0,600;0,700;1,400&display=swap" rel="stylesheet">
<style>
  :root {
    --backdrop: #3a3a3a;
    --card-white: #f7f7f7;
    --ink: #2b2b2b;
    --ink-soft: #444444;
    --silver-mid: #a9a9a9;
    --black: #111111;
    --electric: #1fa3ff;
  }
  * { margin: 0; padding: 0; box-sizing: border-box; }
  html, body { width: 1200px; height: 750px; overflow: hidden; }
  body {
    background: radial-gradient(ellipse at 50% 25%, #555 0%, var(--backdrop) 60%, #2c2c2c 100%);
    font-family: "Open Sans", sans-serif;
    position: relative;
  }
  .card {
    position: absolute;
    top: 228px;
    width: 461px;
    height: 262px;
    overflow: hidden;
    box-shadow: 0 3px 8px rgba(0,0,0,0.45);
  }
  .card--front { left: 124px; background: var(--card-white); }
  .card--back {
    left: 618px;
    background: radial-gradient(ellipse at 40% 35%, #d2d2d2 0%, var(--silver-mid) 75%, #9a9a9a 100%);
  }

  .brand {
    position: absolute;
    display: flex;
    align-items: center;
    gap: 8px;
    font-weight: 700;
    color: var(--ink-soft);
    letter-spacing: 0.5px;
    white-space: nowrap;
  }
  .brand__dot {
    width: 12px; height: 12px;
    border-radius: 50%;
    background: var(--electric);
    flex: none;
  }
  .card--front .brand { left: 32px; top: 42px; font-size: 24px; }

  .contact {
    position: absolute;
    left: 32px;
    top: 132px;
    font-size: 11px;
    line-height: 14px;
    color: var(--ink);
  }
  .contact__address { margin-bottom: 6px; }
  .contact__row {
    display: flex;
    align-items: center;
    gap: 6px;
    height: 17.5px;
  }
  .contact__row svg { width: 11px; height: 11px; flex: none; }

  .holder {
    position: absolute;
    right: 25px;
    top: 149px;
    font-size: 17px;
    font-weight: 600;
    color: var(--ink);
    white-space: nowrap;
  }
  .holder-tab {
    position: absolute;
    right: 0;
    top: 150px;
    width: 9px;
    height: 21px;
    background: var(--electric);
  }
  .footer-band { position: absolute; left: 0; bottom: 0; width: 461px; height: 17px; }

  .runner-art {
    position: absolute;
    left: 200px;
    top: 10px;
    width: 260px;
    height: 250px;
    background: radial-gradient(circle at 60% 45%, rgba(40,40,40,0.55) 0%, rgba(60,60,60,0.28) 35%, rgba(120,120,120,0) 68%);
  }
  .back-accent {
    position: absolute;
    left: 36px;
    top: 181px;
    width: 60px;
    height: 3px;
    background: var(--electric);
  }
  .card--back .brand { left: 36px; top: 190px; font-size: 24px; color: var(--ink-soft); }
  .back-web {
    position: absolute;
    left: 36px;
    top: 227px;
    font-size: 11px;
    font-style: italic;
    color: var(--ink-soft);
    white-space: nowrap;
  }
</style>
</head>
<body>
  <section class="card card--front">
    <div class="brand"><span class="brand__dot"></span>Brisk Inquiries</div>

    <div class="contact">
      <p class="contact__address">PO Box 58<br>Carnwell NSW 2291</p>
      <p class="contact__row">
        <svg viewBox="0 0 12 12"><path d="M2.5 1l2 2.2-1 1.3c.6 1.4 1.6 2.4 3 3l1.3-1 2.2 2-1.2 1.5C5.5 9.8 2.2 6.5 1 3z" fill="#222"/></svg>
        0487 316 204
      </p>
      <p class="contact__row">
        <svg viewBox="0 0 12 12"><rect x="1" y="2.5" width="10" height="7" fill="#222"/><path d="M1 2.8l5 3.6 5-3.6" stroke="#f7f7f7" stroke-width="1" fill="none"/></svg>
        info@briskinquiries-demo.com.au
      </p>
      <p class="contact__row">
        <svg viewBox="0 0 12 12"><circle cx="6" cy="6" r="5" fill="#222"/><path d="M1 6h10M6 1c-2 2.5-2 7.5 0 10M6 1c2 2.5 2 7.5 0 10" stroke="#f7f7f7" stroke-width="0.7" fill="none"/></svg>
        www.briskinquiries-demo.com.au
      </p>
    </div>

    <p class="holder">Morgan Kellaway</p>
    <div class="holder-tab"></div>

    <svg class="footer-band" viewBox="0 0 461 17" preserveAspectRatio="none">
      <defs>
        <linearGradient id="silverBand" x1="0" x2="1" y1="0" y2="0">
          <stop offset="0" stop-color="#8a8a8a"/>
          <stop offset="0.5" stop-color="#d8d8d8"/>
          <stop offset="1" stop-color="#9a9a9a"/>
        </linearGradient>
      </defs>
      <polygon points="0,0 299,0 295,17 0,17" fill="url(#silverBand)"/>
      <polygon points="299,0 302,0 298,17 295,17" fill="#1fa3ff"/>
      <polygon points="302,0 461,0 461,17 298,17" fill="#111111"/>
    </svg>
  </section>

  <section class="card card--back">
    <div class="runner-art" role="img" aria-label="Running magnifying-glass mascot illustration with speed lines"></div>
    <div class="back-accent"></div>
    <div class="brand"><span class="brand__dot"></span>Brisk Inquiries</div>
    <p class="back-web">www.briskinquiries-demo.com.au</p>
  </section>
</body>
</html>
```